Agriculture farming Hemp and CBD

The logo is in works with your company now, should be ready in a few days. We have our Domain (kestrelbrookhollow.com) We would like to see incorporated seed to growth, but not necessary. we would like to nature colors and some black and green. we have our farm and will be growing and selling HEMP and CBD we are based in the state of Virginia. Would like to incorporate the words pause, play, rewind if possible but not necessary.

Target Market(s)

20 years old to elderly

Coding

Coded - Design and coding required

Number of Pages Required

3 page

Font styles to use
Serif

Requirements
Must have
• I'm not sure on the must haves, we are open to any ideas, we would definitely like to see Hemp and CBD included, may the life cycle of seed to plant. We must have a pop up asking if you are 20 years old before they can enter our site and to view or purchase our product. I want the design to be totally different than what i uploaded.
Nice to have
• Would like to see natural colors as well as black and green
Should not have
• I want

```html
<!DOCTYPE html>
<html lang="en">
<head>
<meta charset="utf-8">
<title>Kestrel Brook Hollow – Home Page Layouts</title>
<link href="https://fonts.googleapis.com/css2?family=Roboto:ital,wght@0,400;0,500;0,700;0,900;1,400&display=swap" rel="stylesheet">
<style>
:root{
  --green:#4a9a2a;
  --green-light:#7cc242;
  --green-dark:#2f6e1a;
  --black:#000;
  --ink:#222;
  --muted:#666;
  --paper:#fff;
  --soft:#f5f5f5;
  --earth:#5a3a22;
  --dusk:#3b3a33;
}
*{box-sizing:border-box;margin:0;padding:0}
html,body{width:677px;height:1200px;overflow:hidden;background:var(--paper);font-family:"Roboto",Arial,sans-serif}
.board{position:relative;width:677px;height:1200px;overflow:hidden;background:var(--paper)}
.corner-leaf{position:absolute;width:95px;height:75px;background:radial-gradient(circle at center,#3f8f22 0%,rgba(63,143,34,.55) 45%,rgba(255,255,255,0) 72%)}
.corner-leaf.tl{left:-20px;top:-15px}
.corner-leaf.tr{right:-20px;top:-15px}
.corner-leaf.bl{left:-20px;bottom:-15px}
.corner-leaf.br{right:-20px;bottom:-15px}

.page-frame{position:absolute;top:66px;width:297px;height:1082px;overflow:hidden;box-shadow:0 0 3px rgba(0,0,0,.35)}
.page-frame.light{left:23px}
.page-frame.gated{left:353px}
.page{position:absolute;left:0;top:0;width:637px;height:2323px;transform:scale(.4656);transform-origin:0 0;background:var(--paper);color:var(--ink)}
.abs{position:absolute}

/* nav */
.nav{left:0;top:0;width:637px;height:47px;background:var(--black)}
.logo{left:68px;top:12px;color:#fff;font-size:15px;font-weight:700;letter-spacing:-.2px}
.menu{left:318px;top:16px;display:flex;gap:20px;font-size:10px;color:#fff}
.menu .active{color:var(--green-light)}

/* hero */
.hero{left:0;top:47px;width:637px;height:286px;background:linear-gradient(180deg,#5d6b63 0%,#3d5a3a 35%,#3f7a2a 65%,#2d5e1d 100%)}
.hero-title{left:0;top:170px;width:637px;text-align:center;color:#fff;font-size:28px;font-weight:900;text-shadow:0 2px 4px rgba(0,0,0,.6)}
.dots{left:306px;top:311px;display:flex;gap:5px}
.dots i{width:4px;height:4px;border-radius:50%;background:#fff;opacity:.8}

/* about */
.hex-back{left:40px;top:373px;width:207px;height:225px;background:var(--green);clip-path:polygon(25% 0,75% 0,100% 50%,75% 100%,25% 100%,0 50%)}
.hex{left:28px;top:373px;width:207px;height:225px;background:radial-gradient(circle at 55% 55%,#3e6e25 0%,#6a4a2e 45%,#9c6b48 75%,#7a4c30 100%);clip-path:polygon(25% 0,75% 0,100% 50%,75% 100%,25% 100%,0 50%)}
.h2{font-size:20px;font-weight:700;color:var(--ink)}
.about-title{left:277px;top:390px}
.about-text{left:277px;top:424px;width:280px;font-size:9px;line-height:17.2px;color:#444}
.btn-dark{left:277px;top:574px;width:71px;height:24px;background:var(--ink);color:#fff;font-size:8.5px;font-weight:700;display:flex;align-items:center;justify-content:center;border-radius:2px}

/* services */
.services{left:0;top:613px;width:637px;height:410px;background:linear-gradient(135deg,#3f8f22 0%,#6cb336 40%,#4a9a2a 70%,#2f7a1a 100%)}
.wave{left:0;width:637px}
.svc-title{left:0;top:668px;width:637px;text-align:center;color:#fff}
.svc-sub{left:140px;top:703px;width:357px;text-align:center;color:#fff;font-size:7.5px;line-height:16px}
.card{top:763px;width:158px;height:207px;background:#fff;border-radius:5px 5px 0 0;overflow:hidden}
.card .pic{height:90px}
.card h4{font-size:8.5px;font-weight:700;text-align:center;margin-top:14px;color:var(--ink)}
.card p{font-size:7px;line-height:15.5px;text-align:center;color:#555;padding:6px 8px 0}
.btn-green{height:22px;width:72px;background:var(--green-light);color:#fff;font-size:8px;font-weight:700;display:flex;align-items:center;justify-content:center;border-radius:2px}
.card-btn{top:960px}
.arrow-dot{top:839px;width:18px;height:18px;border-radius:50%;background:#fff;border:1px solid #ccc}

/* blog */
.blog-title{left:0;top:1077px;width:637px;text-align:center}
.blog-big{left:55px;top:1127px;width:168px;height:286px;border:1px solid #e4e4e4;background:#fff}
.blog-big .pic{height:120px}
.date{font-size:7px;color:var(--green)}
.blog-big .date{margin:16px 0 0 16px}
.blog-big h5{font-size:11px;font-weight:700;margin:6px 16px 0;line-height:14px}
.blog-big p{font-size:6.5px;font-weight:700;color:#888;line-height:14.5px;margin:10px 16px 0}
.more{font-size:8.5px;color:var(--green);font-weight:700}
.blog-big .more{margin:10px 0 0 18px}
.blog-row{left:233px;width:340px;height:140px;border:1px solid #e4e4e4;background:#fff;display:flex}
.blog-row .pic{width:135px;height:138px}
.blog-row .body{padding:14px 0 0 18px;width:200px}
.blog-row h5{font-size:11px;font-weight:400;line-height:14px;margin-top:8px}
.blog-row p{font-size:6.3px;color:#999;line-height:14.5px;margin-top:6px}
.blog-row .more{font-weight:400;margin:6px 0 0 3px}

/* band */
.band{left:0;top:1443px;width:637px;height:250px;background:linear-gradient(90deg,#4a4a40 0%,#3a3a33 55%,#2f4a25 100%)}
.band-title{left:0;top:1505px;width:637px;text-align:center;color:#fff;font-size:13.5px;font-weight:700}
.band-text{left:80px;top:1537px;width:477px;text-align:center;color:#fff;font-size:8px;line-height:18.8px}
.band-btn{left:282px;top:1623px}
.band-leaf{left:510px;top:1600px;width:127px;height:140px;background:radial-gradient(circle,#3f8f22 0%,rgba(63,143,34,.5) 45%,rgba(255,255,255,0) 70%)}
.blog-leaf{left:0;top:1020px;width:130px;height:120px;background:radial-gradient(circle at 30% 40%,#3f8f22 0%,rgba(63,143,34,.5) 40%,rgba(255,255,255,0) 68%)}

/* testimonials */
.say-title{left:0;top:1728px;width:637px;text-align:center;font-size:17.5px}
.face{border-radius:50%;border:2px solid var(--green-light)}
.quote-mark{left:532px;top:1775px;font-size:34px;color:var(--green);font-weight:900;letter-spacing:-2px}
.quote{left:312px;top:1811px;width:250px;text-align:center;font-size:7.5px;font-style:italic;line-height:15.5px;color:#444}
.role{left:400px;top:1890px;width:161px;text-align:right;font-size:8.5px;font-weight:700;color:var(--green)}
.origin{left:400px;top:1904px;width:161px;text-align:right;font-size:8.5px;color:#555}
.sq-arrow{top:1933px;width:35px;height:28px;border:1px solid #aaa;display:flex;align-items:center;justify-content:center}

/* contact */
.touch{left:0;top:1996px;width:327px;height:215px;background:linear-gradient(135deg,#3e3e38 0%,#4a4a3f 50%,#33412b 100%)}
.touch-title{left:70px;top:2017px;font-size:15px;font-weight:700;color:#fff}
.field{left:70px;width:160px;height:24px;border-bottom:1px solid #bbb;font-size:7px;color:#fff;padding-top:5px}
.send{left:68px;top:2171px;width:60px;height:20px;background:var(--green);color:#fff;font-size:8.5px;display:flex;align-items:center;justify-content:center}
.reach{left:327px;top:1996px;width:310px;height:215px;background:var(--soft)}
.reach-title{left:365px;top:2015px;font-size:15px;font-weight:700}
.icon{left:365px;width:24px;height:24px;border-radius:50%;background:var(--green);display:flex;align-items:center;justify-content:center}
.reach-text{left:404px;font-size:9px;line-height:18px;color:#333}

/* footer */
.footer{left:0;top:2211px;width:637px;height:112px;background:var(--green)}
.foot-links{left:0;top:2233px;width:637px;display:flex;justify-content:center;gap:18px;color:#fff;font-size:10px}
.socials{left:277px;top:2263px;display:flex;gap:9px}
.socials i{width:19px;height:19px;border-radius:50%;border:1px solid #fff;display:block}
.copy{left:0;top:2296px;width:637px;text-align:center;color:#fff;font-size:6.5px}

/* age gate */
.dim{left:0;top:0;width:637px;height:2323px;background:rgba(0,0,0,.62)}
.gate{left:122px;top:122px;width:392px;height:196px;background:var(--green);color:#fff;text-align:center}
.gate-line{font-size:12.5px;line-height:21px;padding-top:28px}
.gate-ask{font-size:15.5px;font-weight:700;margin-top:10px;letter-spacing:.3px}
.gate-btn{position:absolute;left:149px;top:122px;width:93px;height:34px;border:1.5px solid #fff;font-size:14px;display:flex;align-items:center;justify-content:center}
.gate-leaf{position:absolute;top:60px;width:110px;height:136px;background:radial-gradient(circle at 50% 60%,#8fd05a 0%,rgba(143,208,90,.45) 40%,rgba(74,154,42,0) 70%)}
.gate-close{left:496px;top:126px;width:26px;height:26px;border-radius:50%;background:#fff;display:flex;align-items:center;justify-content:center}
</style>
</head>
<body>
<div class="board">
  <div class="corner-leaf tl" role="img" aria-label="Hemp leaf decoration"></div>
  <div class="corner-leaf tr" role="img" aria-label="Hemp leaf decoration"></div>
  <div class="corner-leaf bl" role="img" aria-label="Hemp leaf decoration"></div>
  <div class="corner-leaf br" role="img" aria-label="Hemp leaf decoration"></div>

  <!-- ===== Home page ===== -->
  <div class="page-frame light">
    <div class="page">
      <header class="abs nav">
        <div class="abs logo">kestrelbrookhollow.com</div>
        <nav class="abs menu"><span class="active">Home</span><span>About</span><span>Services</span><span>Blog</span><span>Contact Us</span></nav>
      </header>
      <section>
        <div class="abs hero" role="img" aria-label="Indoor hemp grow room with rows of young plants under lights"></div>
        <h1 class="abs hero-title">PAUSE. PLAY. REWIND</h1>
        <div class="abs dots"><i></i><i></i><i></i></div>
      </section>
      <section>
        <div class="abs hex-back"></div>
        <div class="abs hex" role="img" aria-label="Hands holding soil with a young hemp seedling"></div>
        <h2 class="abs h2 about-title">ABOUT US</h2>
        <p class="abs about-text">Sed ut perspiciatis unde omnis iste natus error sit voluptatem accusantium doloremque laudantium, totam rem aperiam, eaque ipsa quae ab illo inventore veritatis et quasi architecto beatae vitae dicta sunt explicabo. Nemo enim ipsam voluptatem quia voluptas sit aspernatur aut odit aut fugit, sed quia consequuntur magni dolores eos qui ratione voluptatem sequi nesciunt. Neque porro quisquam est, qui dolorem ipsum quia dolor sit amet.</p>
        <div class="abs btn-dark">READ MORE</div>
      </section>
      <section>
        <div class="abs services" role="img" aria-label="Green hemp leaves background"></div>
        <svg class="abs wave" style="top:605px" width="637" height="35" viewBox="0 0 637 35"><path d="M0 0H637V8C560 2 470 0 380 14C280 28 150 10 0 28Z" fill="#fff"/></svg>
        <svg class="abs wave" style="top:993px" width="637" height="32" viewBox="0 0 637 32"><path d="M0 8C120 28 260 30 380 18C480 8 570 4 637 0V32H0Z" fill="#fff"/></svg>
        <h2 class="abs h2 svc-title">OUR SERVICES</h2>
        <p class="abs svc-sub">Lorem ipsum dolor sit amet, consectetur adipiscing elit, sed do eiusmod tempor incididunt ut labore et dolore magna aliqua.</p>
        <div class="abs arrow-dot" style="left:14px"></div>
        <div class="abs arrow-dot" style="left:577px"></div>
        <article class="abs card" style="left:47px"><div class="pic" role="img" aria-label="Grower inspecting hemp plant" style="background:linear-gradient(135deg,#9dbf6a,#4f7a2e)"></div><h4>Sed ut perspiciatis unde</h4><p>Sed ut perspiciatis unde omnis iste natus error sit voluptatem accusantium doloremque laudantium, totam rem aperiam, eaque ipsa quae ab illo</p></article>
        <article class="abs card" style="left:227px"><div class="pic" role="img" aria-label="Rows of hemp in an open field" style="background:linear-gradient(180deg,#b9cfe0 0%,#6f9a4a 35%,#4a6e2e 100%)"></div><h4>Lorem ipsum dolor sit amet</h4><p>Sed ut perspiciatis unde omnis iste natus error sit voluptatem accusantium doloremque laudantium, totam rem aperiam, eaque ipsa quae ab illo</p></article>
        <article class="abs card" style="left:404px"><div class="pic" role="img" aria-label="Hands tending hemp leaves" style="background:linear-gradient(135deg,#2f5a22,#6f9a4a)"></div><h4>Sed ut perspiciatis unde</h4><p>Sed ut perspiciatis unde omnis iste natus error sit voluptatem accusantium doloremque laudantium, totam rem aperiam, eaque ipsa quae ab illo</p></article>
        <div class="abs btn-green card-btn" style="left:90px">READ MORE</div>
        <div class="abs btn-green card-btn" style="left:270px">READ MORE</div>
        <div class="abs btn-green card-btn" style="left:447px">READ MORE</div>
      </section>
      <section>
        <div class="abs blog-leaf" role="img" aria-label="Hemp leaf decoration"></div>
        <h2 class="abs h2 blog-title">LATEST BLOG</h2>
        <article class="abs blog-big"><div class="pic" role="img" aria-label="Hemp grow room" style="background:linear-gradient(180deg,#6d7a70,#3f7a2a)"></div><div class="date">Sep,2020</div><h5>Sed ut perspiciatis unde omnis iste natus</h5><p>Ut enim ad minima veniaquis nostrererci tationem ullam corporisosan isi utliquid ex ea commodi eprehenderitq ui in ea voluptmmodate velit .</p><div class="more">READ MORE »</div></article>
        <article class="abs blog-row" style="top:1127px"><div class="pic" role="img" aria-label="Hemp leaf held up to light" style="background:linear-gradient(135deg,#c9d9a8,#5d8f3a)"></div><div class="body"><div class="date">Sep,2020</div><h5>Sed ut perspiciatis unde omnis iste natus error</h5><p>Ut enim ad minima veniam, quis nostrererci tationem ullam corporis suscipit laboriosan isi ut aliquid ex ea eprehenderitq utate velit .</p><div class="more">READ MORE »</div></div></article>
        <article class="abs blog-row" style="top:1275px"><div class="pic" role="img" aria-label="Gloved hand checking a hemp plant" style="background:linear-gradient(135deg,#6fa0d8,#5d8f3a)"></div><div class="body"><div class="date">Sep,2020</div><h5>Sed ut perspiciatis unde omnis iste natus error</h5><p>Ut enim ad minima veniam, quis nostrererci tationem ullam corporis suscipit laboriosan isi ut aliquid ex ea eprehenderitq utate velit .</p><div class="more">READ MORE »</div></div></article>
      </section>
      <section>
        <div class="abs band" role="img" aria-label="Grower holding a hemp plant, dark tone"></div>
        <svg class="abs wave" style="top:1440px" width="637" height="30" viewBox="0 0 637 30"><path d="M0 0H637V14C470 24 260 26 0 2Z" fill="#fff"/></svg>
        <svg class="abs wave" style="top:1665px" width="637" height="30" viewBox="0 0 637 30"><path d="M0 28C200 14 430 6 637 18V30H0Z" fill="#fff"/></svg>
        <h2 class="abs band-title">LOREM IPSUM DOLOR SIT AMET, CONSECTETUR</h2>
        <p class="abs band-text">At vero eos et accusamus et iusto odio dignissimos ducimus qui blanditiis praesentium voluptatum deleniti atque corrupti quos dolores et quas molestias excepturi sint occaecati cupiditate non provident, similique sunt in culpa qui officia deserunt mollitia animi, id est laborum et dolorum fuga. Et harum quidem rerum facilis est et expedita distinctio. Nam libero tempore, cum soluta nobis est eligendi optio cumque .</p>
        <div class="abs btn-green band-btn">READ MORE</div>
        <div class="abs band-leaf" role="img" aria-label="Hemp leaf decoration"></div>
      </section>
      <section>
        <h2 class="abs h2 say-title">THAT'S WHAT OUR CUSTOMERS SAY</h2>
        <div class="abs face" style="left:60px;top:1799px;width:58px;height:58px;background:#c9a27e" role="img" aria-label="Customer portrait"></div>
        <div class="abs face" style="left:119px;top:1871px;width:58px;height:58px;background:#8a5a40" role="img" aria-label="Customer portrait"></div>
        <div class="abs face" style="left:49px;top:1913px;width:46px;height:46px;background:#3a8fd0" role="img" aria-label="Customer portrait"></div>
        <div class="abs face" style="left:180px;top:1782px;width:132px;height:132px;background:#b58a6a" role="img" aria-label="Featured customer portrait"></div>
        <div class="abs quote-mark">“</div>
        <p class="abs quote">Sed ut perspiciatis unde omnis iste natus error sit voluptatem accusantium doloremque laudantium, totam rem aperiam, eaque ipsa quae ab illo inventore veritatis et quasi architecto beatae vitae dicta sunt explicabo. Nemo enim ipsam voluptatem quia voluptas</p>
        <div class="abs role">CEO</div>
        <div class="abs origin">Hong Kong based Exporter</div>
        <div class="abs sq-arrow" style="left:479px"><svg width="16" height="10" viewBox="0 0 16 10"><path d="M15 5H2M6 1L2 5l4 4" stroke="#222" stroke-width="1.5" fill="none"/></svg></div>
        <div class="abs sq-arrow" style="left:538px"><svg width="16" height="10" viewBox="0 0 16 10"><path d="M1 5h13M10 1l4 4-4 4" stroke="#888" stroke-width="1.5" fill="none"/></svg></div>
      </section>
      <section>
        <div class="abs touch" role="img" aria-label="Hands holding hemp, dark tone"></div>
        <h3 class="abs touch-title">GET IN TOUCH</h3>
        <div class="abs field" style="top:2048px">Name</div>
        <div class="abs field" style="top:2074px">Email</div>
        <div class="abs field" style="top:2100px">Phone</div>
        <div class="abs field" style="top:2132px">Message</div>
        <div class="abs send">SEND</div>
        <div class="abs reach"></div>
        <h3 class="abs reach-title">CONTACT US</h3>
        <div class="abs icon" style="top:2053px"><svg width="10" height="12" viewBox="0 0 10 12"><path d="M5 0a4 4 0 014 4c0 3-4 8-4 8S1 7 1 4a4 4 0 014-4z" fill="#fff"/><circle cx="5" cy="4" r="1.5" fill="#4a9a2a"/></svg></div>
        <div class="abs icon" style="top:2107px"><svg width="11" height="11" viewBox="0 0 11 11"><path d="M2 0l2 2.5-1 1.5c.8 1.6 2 2.8 3.5 3.5l1.5-1L10.5 8.5 9 10.5C4.5 10 .5 6 0 1.5z" fill="#fff"/></svg></div>
        <div class="abs icon" style="top:2147px"><svg width="12" height="9" viewBox="0 0 12 9"><rect x=".5" y=".5" width="11" height="8" fill="none" stroke="#fff"/><path d="M.5 .5L6 5l5.5-4.5" stroke="#fff" fill="none"/></svg></div>
        <div class="abs reach-text" style="top:2053px">Fenwick Mill 2nd Floor, Orchard House<br>Larkspur Road Ashby, Virginia</div>
        <div class="abs reach-text" style="top:2110px">Tel:&nbsp; 0140 555 0172</div>
        <div class="abs reach-text" style="top:2150px">Email: info@kestrelbrookhollow.com</div>
      </section>
      <footer>
        <div class="abs footer"></div>
        <nav class="abs foot-links"><span>Home</span><span>About</span><span>Services</span><span>Blog</span><span>Contact Us</span></nav>
        <div class="abs socials"><i></i><i></i><i></i></div>
        <div class="abs copy">Copyrights © 2020 Copyrights Company Name | All Rights Reserved</div>
      </footer>
    </div>
  </div>

  <!-- ===== Home page with age check ===== -->
  <div class="page-frame gated">
    <div class="page">
      <header class="abs nav">
        <div class="abs logo">kestrelbrookhollow.com</div>
        <nav class="abs menu"><span class="active">Home</span><span>About</span><span>Services</span><span>Blog</span><span>Contact Us</span></nav>
      </header>
      <div class="abs hero" role="img" aria-label="Indoor hemp grow room with rows of young plants under lights"></div>
      <div class="abs hex-back"></div>
      <div class="abs hex" role="img" aria-label="Hands holding soil with a young hemp seedling"></div>
      <h2 class="abs h2 about-title">ABOUT US</h2>
      <p class="abs about-text">Sed ut perspiciatis unde omnis iste natus error sit voluptatem accusantium doloremque laudantium, totam rem aperiam, eaque ipsa quae ab illo inventore veritatis et quasi architecto beatae vitae dicta sunt explicabo. Nemo enim ipsam voluptatem quia voluptas sit aspernatur aut odit aut fugit, sed quia consequuntur magni dolores eos qui ratione voluptatem sequi nesciunt. Neque porro quisquam est, qui dolorem ipsum quia dolor sit amet.</p>
      <div class="abs btn-dark">READ MORE</div>
      <div class="abs services" role="img" aria-label="Green hemp leaves background"></div>
      <svg class="abs wave" style="top:605px" width="637" height="35" viewBox="0 0 637 35"><path d="M0 0H637V8C560 2 470 0 380 14C280 28 150 10 0 28Z" fill="#fff"/></svg>
      <svg class="abs wave" style="top:993px" width="637" height="32" viewBox="0 0 637 32"><path d="M0 8C120 28 260 30 380 18C480 8 570 4 637 0V32H0Z" fill="#fff"/></svg>
      <h2 class="abs h2 svc-title">OUR SERVICES</h2>
      <p class="abs svc-sub">Lorem ipsum dolor sit amet, consectetur adipiscing elit, sed do eiusmod tempor incididunt ut labore et dolore magna aliqua.</p>
      <div class="abs arrow-dot" style="left:14px"></div>
      <div class="abs arrow-dot" style="left:577px"></div>
      <article class="abs card" style="left:47px"><div class="pic" role="img" aria-label="Grower inspecting hemp plant" style="background:linear-gradient(135deg,#9dbf6a,#4f7a2e)"></div><h4>Digital Due Diligence</h4><p>Sed ut perspiciatis unde omnis iste natus error sit voluptatem accusantium doloremque laudantium, totam rem aperiam, eaque ipsa quae ab illo</p></article>
      <article class="abs card" style="left:227px"><div class="pic" role="img" aria-label="Rows of hemp in an open field" style="background:linear-gradient(180deg,#b9cfe0 0%,#6f9a4a 35%,#4a6e2e 100%)"></div><h4>New Agency Selection Support</h4><p>Sed ut perspiciatis unde omnis iste natus error sit voluptatem accusantium doloremque laudantium, totam rem aperiam, eaque ipsa quae ab illo</p></article>
      <article class="abs card" style="left:404px"><div class="pic" role="img" aria-label="Hands tending hemp leaves" style="background:linear-gradient(135deg,#2f5a22,#6f9a4a)"></div><h4>Existing Agency Auditing Service</h4><p>Sed ut perspiciatis unde omnis iste natus error sit voluptatem accusantium doloremque laudantium, totam rem aperiam, eaque ipsa quae ab illo</p></article>
      <div class="abs btn-green card-btn" style="left:90px">READ MORE</div>
      <div class="abs btn-green card-btn" style="left:270px">READ MORE</div>
      <div class="abs btn-green card-btn" style="left:447px">READ MORE</div>
      <div class="abs blog-leaf" role="img" aria-label="Hemp leaf decoration"></div>
      <h2 class="abs h2 blog-title">LATEST BLOG</h2>
      <article class="abs blog-big"><div class="pic" role="img" aria-label="Hemp grow room" style="background:linear-gradient(180deg,#6d7a70,#3f7a2a)"></div><div class="date">April,2020</div><h5>Sed ut perspiciatis unde omnis iste natus</h5><p>Ut enim ad minima veniaquis nostrererci tationem ullam corporisosan isi utliquid ex ea commodi eprehenderitq ui in ea voluptmmodate velit .</p><div class="more">READ MORE »</div></article>
      <article class="abs blog-row" style="top:1127px"><div class="pic" role="img" aria-label="Hemp leaf held up to light" style="background:linear-gradient(135deg,#c9d9a8,#5d8f3a)"></div><div class="body"><div class="date">April,2020</div><h5>Sed ut perspiciatis unde omnis iste natus error</h5><p>Ut enim ad minima veniam, quis nostrererci tationem ullam corporis suscipit laboriosan isi ut aliquid ex ea eprehenderitq utate velit .</p><div class="more">READ MORE »</div></div></article>
      <article class="abs blog-row" style="top:1275px"><div class="pic" role="img" aria-label="Gloved hand checking a hemp plant" style="background:linear-gradient(135deg,#6fa0d8,#5d8f3a)"></div><div class="body"><div class="date">April,2020</div><h5>Sed ut perspiciatis unde omnis iste natus error</h5><p>Ut enim ad minima veniam, quis nostrererci tationem ullam corporis suscipit laboriosan isi ut aliquid ex ea eprehenderitq utate velit .</p><div class="more">READ MORE »</div></div></article>
      <div class="abs band" role="img" aria-label="Grower holding a hemp plant, dark tone"></div>
      <svg class="abs wave" style="top:1440px" width="637" height="30" viewBox="0 0 637 30"><path d="M0 0H637V14C470 24 260 26 0 2Z" fill="#fff"/></svg>
      <svg class="abs wave" style="top:1665px" width="637" height="30" viewBox="0 0 637 30"><path d="M0 28C200 14 430 6 637 18V30H0Z" fill="#fff"/></svg>
      <h2 class="abs band-title">LOREM IPSUM DOLOR SIT AMET, CONSECTETUR</h2>
      <p class="abs band-text">At vero eos et accusamus et iusto odio dignissimos ducimus qui blanditiis praesentium voluptatum deleniti atque corrupti quos dolores et quas molestias excepturi sint occaecati cupiditate non provident, similique sunt in culpa qui officia deserunt mollitia animi, id est laborum et dolorum fuga. Et harum quidem rerum facilis est et expedita distinctio. Nam libero tempore, cum soluta nobis est eligendi optio cumque .</p>
      <div class="abs btn-green band-btn">READ MORE</div>
      <div class="abs band-leaf" role="img" aria-label="Hemp leaf decoration"></div>
      <h2 class="abs h2 say-title">THAT'S WHAT OUR CUSTOMERS SAY</h2>
      <div class="abs face" style="left:60px;top:1799px;width:58px;height:58px;background:#c9a27e" role="img" aria-label="Customer portrait"></div>
      <div class="abs face" style="left:119px;top:1871px;width:58px;height:58px;background:#8a5a40" role="img" aria-label="Customer portrait"></div>
      <div class="abs face" style="left:49px;top:1913px;width:46px;height:46px;background:#3a8fd0" role="img" aria-label="Customer portrait"></div>
      <div class="abs face" style="left:180px;top:1782px;width:132px;height:132px;background:#b58a6a" role="img" aria-label="Featured customer portrait"></div>
      <div class="abs quote-mark">“</div>
      <p class="abs quote">Sed ut perspiciatis unde omnis iste natus error sit voluptatem accusantium doloremque laudantium, totam rem aperiam, eaque ipsa quae ab illo inventore veritatis et quasi architecto beatae vitae dicta sunt explicabo. Nemo enim ipsam voluptatem quia voluptas</p>
      <div class="abs role">CEO</div>
      <div class="abs origin">Hong Kong based Exporter</div>
      <div class="abs sq-arrow" style="left:479px"><svg width="16" height="10" viewBox="0 0 16 10"><path d="M15 5H2M6 1L2 5l4 4" stroke="#222" stroke-width="1.5" fill="none"/></svg></div>
      <div class="abs sq-arrow" style="left:538px"><svg width="16" height="10" viewBox="0 0 16 10"><path d="M1 5h13M10 1l4 4-4 4" stroke="#888" stroke-width="1.5" fill="none"/></svg></div>
      <div class="abs touch" role="img" aria-label="Hands holding hemp, dark tone"></div>
      <h3 class="abs touch-title">GET IN TOUCH</h3>
      <div class="abs field" style="top:2048px">Name</div>
      <div class="abs field" style="top:2074px">Email</div>
      <div class="abs field" style="top:2100px">Phone</div>
      <div class="abs field" style="top:2132px">Message</div>
      <div class="abs send">SEND</div>
      <div class="abs reach"></div>
      <h3 class="abs reach-title">CONTACT US</h3>
      <div class="abs icon" style="top:2053px"></div>
      <div class="abs icon" style="top:2107px"></div>
      <div class="abs icon" style="top:2147px"></div>
      <div class="abs reach-text" style="top:2053px">Fenwick Mill 2nd Floor, Orchard House<br>Larkspur Road Ashby, Virginia</div>
      <div class="abs reach-text" style="top:2110px">Tel:&nbsp; 0140 555 0172</div>
      <div class="abs reach-text" style="top:2150px">Email: info@kestrelbrookhollow.com</div>
      <div class="abs footer"></div>
      <nav class="abs foot-links"><span>Home</span><span>About</span><span>Services</span><span>Blog</span><span>Contact Us</span></nav>
      <div class="abs socials"><i></i><i></i><i></i></div>
      <div class="abs copy">Copyrights © 2020 Copyrights Company Name | All Rights Reserved</div>

      <div class="abs dim"></div>
      <div class="abs gate" role="dialog" aria-label="Age check">
        <div class="gate-leaf" style="left:8px" role="img" aria-label="Hemp leaf decoration"></div>
        <div class="gate-leaf" style="right:8px" role="img" aria-label="Hemp leaf decoration"></div>
        <p class="gate-line">THIS WEBSITE REQUIRES YOU TO BE 18 YEARS<br>OR OLDER TO ENTER</p>
        <p class="gate-ask">ARE YOU OVER 18?</p>
        <div class="gate-btn">YES, I AM</div>
      </div>
      <div class="abs gate-close"><svg width="12" height="12" viewBox="0 0 12 12"><path d="M2 2l8 8M10 2l-8 8" stroke="#000" stroke-width="2.6"/></svg></div>
    </div>
  </div>
</div>
</body>
</html>
```